LA's Newest HEMP Facial Oil and Body Oil Packaging Project

We need a packaging concept for a Hemp based facial oil and body oil. We need label design for the bottle and carton graphics. I am attaching a few reference photos. The target demographic is women between 17-35 year old. Products need to be able to stand out in crowded stores with clear calls to action.
1oz Dropper Bottle with Unit Carton - Hemp Facial Oil
4oz PET Bottle with Unit Carton - Hemp + Rose Facial Oil

```html
<!DOCTYPE html>
<html lang="en">
<head>
<meta charset="utf-8">
<title>Hemp Facial Oil – Carton and Bottle Label</title>
<link rel="stylesheet" href="https://fonts.googleapis.com/css2?family=Montserrat:wght@700&family=Raleway:wght@200;400&display=swap">
<style>
  :root {
    --page-bg: #f4f4f5;
    --panel-white: #ffffff;
    --band-purple: #9a6bb0;
    --band-purple-dark: #8a5ca2;
    --title-purple: #8f5aa9;
    --ink: #3a3a3a;
    --floral-pink: #e58fb3;
    --floral-rose: #f3c2d4;
    --floral-lilac: #b9a6d6;
  }
  * { margin: 0; padding: 0; box-sizing: border-box; }
  html, body {
    width: 1200px; height: 1200px; overflow: hidden;
    background: var(--page-bg);
  }
  .canvas { position: relative; width: 1200px; height: 1200px; }

  .carton-front, .bottle-label {
    position: absolute;
    background: var(--panel-white);
    overflow: hidden;
    box-shadow: 0 2px 14px rgba(0,0,0,0.08);
  }
  .carton-front { left: 230px; top: 90px; width: 300px; height: 1020px; }
  .bottle-label { left: 650px; top: 370px; width: 320px; height: 460px; }

  .floral {
    position: absolute;
    background:
      radial-gradient(circle at 35% 40%, var(--floral-rose) 0 12%, transparent 30%),
      radial-gradient(circle at 65% 55%, var(--floral-pink) 0 8%, transparent 28%),
      radial-gradient(circle at 50% 50%, var(--floral-lilac) 0 20%, transparent 62%);
    opacity: 0.85;
  }
  .carton-front .floral-top { right: -20px; top: -10px; width: 300px; height: 330px; }
  .carton-front .floral-bottom { left: 0; bottom: -10px; width: 310px; height: 320px; }
  .bottle-label .floral-top { left: -30px; top: -10px; width: 190px; height: 170px; }
  .bottle-label .floral-bottom { right: -30px; bottom: -20px; width: 200px; height: 190px; }

  .product-type {
    position: absolute; left: 0; right: 0;
    font-family: "Montserrat", sans-serif;
    font-weight: 700;
    color: var(--title-purple);
    text-align: center;
    letter-spacing: 0.5px;
  }
  .carton-front .product-type { top: 340px; font-size: 38px; }
  .bottle-label .product-type { top: 325px; font-size: 31px; }

  .name-band {
    position: absolute; left: 0; right: 0;
    background: linear-gradient(90deg, var(--band-purple-dark), var(--band-purple));
    display: flex; align-items: center; justify-content: center;
  }
  .carton-front .name-band { top: 390px; height: 260px; }
  .bottle-label .name-band { top: 140px; height: 170px; }

  .product-name {
    font-family: "Raleway", sans-serif;
    font-weight: 200;
    color: var(--panel-white);
    line-height: 1;
    letter-spacing: -2px;
  }
  .carton-front .product-name { font-size: 112px; margin-top: -14px; }
  .bottle-label .product-name { font-size: 104px; margin-top: -12px; }

  .volume {
    position: absolute;
    font-family: "Raleway", sans-serif;
    font-weight: 400;
    color: var(--ink);
  }
  .carton-front .volume { left: 0; right: 0; top: 668px; text-align: center; font-size: 27px; }
  .bottle-label .volume { left: 16px; top: 418px; font-size: 18px; }
</style>
</head>
<body>
<main class="canvas">
  <section class="carton-front" aria-label="Unit carton front panel">
    <div class="floral floral-top" role="img" aria-label="Watercolour pink and lilac floral sprays"></div>
    <h1 class="product-type">FACIAL OIL</h1>
    <div class="name-band"><span class="product-name">hemp</span></div>
    <p class="volume">1 oz / 30 ml</p>
    <div class="floral floral-bottom" role="img" aria-label="Watercolour pink and lilac floral sprays"></div>
  </section>

  <section class="bottle-label" aria-label="Dropper bottle label">
    <div class="floral floral-top" role="img" aria-label="Watercolour pink and lilac floral sprays"></div>
    <div class="name-band"><span class="product-name">hemp</span></div>
    <h2 class="product-type">FACIAL OIL</h2>
    <div class="floral floral-bottom" role="img" aria-label="Watercolour pink and lilac floral sprays"></div>
    <p class="volume">1 oz / 30 ml</p>
  </section>
</main>
</body>
</html>
```